We need a logo design that explain all the products we possess.
The main goal is to represent graphically all the logos, pointing to one single logo - Vellamor.
The descriptions are in french.
I have uploaded a file with 4 logos to use:
Vellamor (the logo that all the rest should be pointing to)
RTN
Ombrevik
TroupéLune
All logo must be used in the vector graphic format, the description file is in each folder, it's the description that should be next to the logo.

The main goal of this is to create a banner 10' x 11' (estimated)

Target Market(s)

Cities

Requirements
Must have
• All the logos in the zip file in vector graphic.
Nice to have
• A background
Should not have
• Do not use KOL logo, it's a mix with RTN, and Kol Blue/dark blue with inscription "RTN", Charging fees for a part of the picture is not ok!

```html
<!DOCTYPE html>
<html lang="fr">
<head>
<meta charset="utf-8">
<title>Portail Vellamors 2.0 — Bannière</title>
<link rel="stylesheet" href="https://fonts.googleapis.com/css2?family=Montserrat:wght@600;700;800&display=swap">
<style>
  :root {
    --page-bg: #ececec;
    --sky-top: #6fa6df;
    --sky-mid: #a9cbec;
    --sky-low: #e4eef8;
    --city-light: #c7d6e6;
    --city-dark: #46607f;
    --ring-grey: #e3e4e6;
    --ring-white: #ffffff;
    --outline: #1d1d1f;
    --green: #8cc63f;
    --teal: #5ea3a8;
    --blue: #1e9be0;
    --brand-blue: #1b75bc;
    --label: #111111;
    --band: #8cc63f;
  }
  * { margin: 0; padding: 0; box-sizing: border-box; }
  html, body {
    width: 779px;
    height: 1200px;
    overflow: hidden;
    background: var(--page-bg);
  }
  .banner {
    position: absolute;
    left: 29.5px;
    top: 204px;
    width: 720px;
    height: 792px;
    box-shadow: 0 4px 14px rgba(0, 0, 0, 0.12);
  }
  .banner svg { display: block; width: 100%; height: 100%; }
  .label {
    font-family: "Montserrat", sans-serif;
    font-weight: 700;
    font-size: 22px;
    fill: var(--label);
    text-anchor: middle;
  }
  .brand-name {
    font-family: "Montserrat", sans-serif;
    font-weight: 800;
    text-anchor: middle;
  }
</style>
</head>
<body>
<main class="banner">
  <svg viewBox="0 0 896 985" xmlns="http://www.w3.org/2000/svg">
    <defs>
      <linearGradient id="sky" x1="0" y1="0" x2="0" y2="1">
        <stop offset="0" stop-color="var(--sky-top)"/>
        <stop offset="0.45" stop-color="var(--sky-mid)"/>
        <stop offset="0.72" stop-color="var(--sky-low)"/>
      </linearGradient>
      <linearGradient id="city" x1="0" y1="0" x2="0" y2="1">
        <stop offset="0" stop-color="var(--city-light)"/>
        <stop offset="0.45" stop-color="#7d93ad"/>
        <stop offset="1" stop-color="var(--city-dark)"/>
      </linearGradient>
    </defs>

    <!-- background -->
    <rect class="sky" width="896" height="985" fill="url(#sky)"/>
    <g class="city-skyline" role="img" aria-label="Photo panoramique d'une ville avec gratte-ciel">
      <rect x="0" y="700" width="896" height="272" fill="url(#city)"/>
    </g>
    <rect class="bottom-band" x="0" y="971" width="896" height="14" fill="var(--band)"/>

    <!-- hub outline -->
    <g class="hub-outline" fill="none" stroke="var(--outline)" stroke-width="2.5">
      <path d="M233 275 A217 217 0 0 1 667 275"/>
      <path d="M233 275 A217 217 0 0 0 258 376" stroke-dasharray="7 5"/>
      <path d="M667 275 A217 217 0 0 1 642 376" stroke-dasharray="7 5"/>
    </g>
    <path class="hub-connector" d="M262 383 A217 217 0 0 0 638 383" fill="none" stroke="#4a86c5" stroke-width="2.5" stroke-dasharray="7 5"/>
    <circle cx="233" cy="275" r="8" fill="#fff" stroke="var(--outline)" stroke-width="3"/>
    <circle cx="667" cy="275" r="8" fill="#fff" stroke="var(--outline)" stroke-width="3"/>

    <!-- hub -->
    <circle cx="450" cy="275" r="196" fill="var(--ring-grey)"/>
    <circle cx="452" cy="270" r="166" fill="var(--ring-white)"/>
    <g class="hub-brand">
      <circle cx="450" cy="225" r="26" fill="var(--brand-blue)"/>
      <text class="brand-name" x="450" y="306" font-size="34" fill="var(--brand-blue)">VELLAMOR</text>
      <text class="label" x="448" y="352" font-size="23">PORTAIL</text>
      <text class="label" x="448" y="382" font-size="23">VELLAMORS 2.0</text>
    </g>

    <!-- arrows into hub -->
    <path d="M245 390 Q262 366 286 358" fill="none" stroke="var(--green)" stroke-width="9"/>
    <polygon points="262,346 300,340 292,378" fill="var(--green)"/>
    <path d="M655 390 Q638 366 614 358" fill="none" stroke="var(--blue)" stroke-width="9"/>
    <polygon points="638,346 600,340 608,378" fill="var(--blue)"/>
    <polygon points="420,450 447,415 474,450" fill="var(--teal)"/>

    <!-- product: RTN -->
    <g class="product product-rtn">
      <circle cx="212" cy="440" r="82" fill="#fff" stroke="var(--green)" stroke-width="11"/>
      <rect x="200" y="418" width="24" height="24" fill="var(--brand-blue)"/>
      <text class="brand-name" x="212" y="488" font-size="24" fill="var(--brand-blue)">RTN</text>
      <text class="label" x="208" y="560">CONSEIL</text>
      <text class="label" x="208" y="591">SANS PAPIER</text>
    </g>

    <!-- product: Ombrevik -->
    <g class="product product-ombrevik">
      <circle cx="447" cy="535" r="80" fill="#fff" stroke="var(--teal)" stroke-width="11"/>
      <circle cx="447" cy="520" r="16" fill="#3a8fd0"/>
      <text class="brand-name" x="447" y="570" font-size="15" letter-spacing="2" fill="#2a7fc1">OMBREVIK</text>
      <text class="label" x="450" y="651">PERMIS | CARTE</text>
      <text class="label" x="450" y="681">INVENTAIRE | TAXES</text>
    </g>

    <!-- product: TroupéLune -->
    <g class="product product-troupelune">
      <circle cx="682" cy="440" r="80" fill="#fff" stroke="var(--blue)" stroke-width="11"/>
      <circle cx="682" cy="418" r="18" fill="var(--blue)"/>
      <text class="brand-name" x="682" y="470" font-size="20" fill="var(--blue)">TroupéLune</text>
      <text class="label" x="690" y="560">LICENCES</text>
      <text class="label" x="690" y="591">POUR ANIMAUX</text>
    </g>
  </svg>
</main>
</body>
</html>
```